Company Profile for Academic and Study Abroad Services

I am looking for Power Point Design for company Profile . the company is academic and study abroad services. you can visit the website which is www.korvapath.ae . the colour i prefer is Dark Blue + White + Black . you can find all the content for power point and logo and some picture i need you to add it.

Target Market(s)

Students who wants to study abroad. Universities . Learning centre.

Industry/Entity Type

Education

Font styles to use
Serif
Sans Serif

Colors
0555a3
ffffff
000000
aaaaaa

Requirements
Must have
• Must Have Images for each slides.
Nice to have
• infographic. Images related to the study abroad

```html
<!DOCTYPE html>
<html lang="en">
<head>
<meta charset="utf-8">
<title>KORVA PATH – Company Profile</title>
<link href="https://fonts.googleapis.com/css2?family=Montserrat:wght@400;500;600;700;800&family=Open+Sans:wght@400;600;700&display=swap" rel="stylesheet">
<style>
:root{
  --blue:#0555a3;
  --black:#000000;
  --white:#ffffff;
  --grey:#aaaaaa;
  --light:#e3e3ef;
  --ink:#222222;
  --muted:#555555;
  --map:#a8a8a8;
}
*{box-sizing:border-box;margin:0;padding:0}
html,body{width:1200px;height:1135px;overflow:hidden;background:var(--light)}
body{font-family:"Open Sans",Arial,sans-serif;color:var(--ink)}
.board{display:grid;grid-template-columns:repeat(3,1fr);grid-template-rows:repeat(5,1fr);gap:4px;padding:4px;width:1200px;height:1135px}
.slide{position:relative;background:var(--white);overflow:hidden}
.photo{position:absolute;background:linear-gradient(135deg,#8a8f99,#c9c3b8)}
.brand{font-family:"Montserrat",Arial,sans-serif;font-weight:800;color:var(--black);letter-spacing:.5px;line-height:1;text-align:center}
.title{font-family:"Montserrat",Arial,sans-serif;font-weight:700;color:var(--black);line-height:1}
.subtitle{font-family:"Open Sans",Arial,sans-serif;color:var(--ink)}
.contacts{font-size:6px;color:#888;line-height:1.5}
.tiny{font-size:6px;line-height:1.45;color:var(--ink)}

/* cover 1 */
.cover1 .photo{left:0;top:0;width:100%;height:56%;background:linear-gradient(180deg,#dfe6ee 0%,#b9a993 55%,#6f7b94 100%)}
.cover1 .logo-box{position:absolute;left:50%;top:47%;transform:translate(-50%,-50%);width:58px;height:50px;background:var(--white);display:flex;align-items:center;justify-content:center}
.cover1 .logo-box .brand{font-size:11px}
.cover1 .title{position:absolute;top:153px;width:100%;text-align:center;font-size:27px}
.cover1 .subtitle{position:absolute;top:190px;width:100%;text-align:center;font-size:13px}
.cover1 .contacts{position:absolute;bottom:6px;width:100%;text-align:center;font-size:4.5px;word-spacing:10px}

/* cover 2 */
.cover2 .map{position:absolute;right:0;top:0;width:62%;height:100%;background:radial-gradient(ellipse at 60% 40%,#9d9d9d,#b9b9b9 60%,#e8e8e8 100%)}
.cover2 .brand{position:absolute;left:14px;top:30px;font-size:14px;text-align:left}
.cover2 .title{position:absolute;left:14px;top:68px;font-size:27px;z-index:1}
.cover2 .subtitle{position:absolute;left:14px;top:100px;font-size:13px;z-index:1}
.cover2 .contacts{position:absolute;left:14px;top:124px;z-index:1}

/* cover 3 */
.cover3 .map{position:absolute;left:8%;top:5%;width:88%;height:90%;background:radial-gradient(ellipse at 50% 50%,#ececec,#f7f7f7 60%,var(--white) 100%)}
.cover3 .brand{position:absolute;left:0;width:100%;top:30px;font-size:14px}
.cover3 .title{position:absolute;left:100px;top:84px;font-size:27px}
.cover3 .subtitle{position:absolute;left:100px;top:116px;font-size:13px}
.cover3 .contacts{position:absolute;left:12px;top:118px}

/* quotes */
.quote{position:absolute;text-align:center;width:140px;font-size:7.5px;line-height:1.35;color:#444}
.quote .mark{display:block;font-family:"Montserrat",Arial,sans-serif;font-weight:800;font-size:12px;color:#888;line-height:1}
.quote .by{display:block;margin-top:2px;font-size:7px;color:#777;font-weight:600}
.portrait{position:absolute;width:86px;height:86px;border-radius:50%;background:radial-gradient(circle,#6d6d6d,#2a2a2a);border:3px solid #8a8a8a}
.portrait.warm{background:radial-gradient(circle,#c9b8a8,#7e6a58)}
.portrait.dark{border-color:#0c1a33}
.vline{position:absolute;width:2px;background:#b5b5b5}
.vline.dark{background:#0c1a33}
.hline{position:absolute;height:2px;background:#0c1a33}
.corner-brand{position:absolute;right:8px;bottom:6px;font-family:"Montserrat",Arial,sans-serif;font-weight:800;font-size:8px;color:var(--black)}

/* overview */
.overview .strip{position:absolute;top:0;left:0;width:100%;height:74px;display:grid;grid-template-columns:repeat(4,1fr)}
.overview .strip div{background:linear-gradient(135deg,#5d6470,#c4bdb2)}
.overview .strip div:nth-child(2){background:linear-gradient(135deg,#808a80,#dcd8cc)}
.overview .strip div:nth-child(3){background:linear-gradient(135deg,#3f4a3a,#9aa48b)}
.overview .strip div:nth-child(4){background:linear-gradient(135deg,#a89a86,#e8e2d6)}
.overview .tags{position:absolute;top:69px;left:0;width:100%;display:grid;grid-template-columns:repeat(4,1fr);gap:8px;padding:0 6px 0 22px}
.overview .tag{background:var(--blue);color:var(--white);font-size:6.5px;font-weight:700;text-align:center;padding:2px 0;font-family:"Montserrat",Arial,sans-serif}
.overview .cols{position:absolute;top:84px;left:0;width:100%;height:136px;display:grid;grid-template-columns:repeat(4,1fr);gap:4px;padding:0 4px;align-items:center}
.overview .cols p{font-size:5.3px;line-height:1.35;text-align:center}

/* banner slides */
.banner .band{position:absolute;left:0;top:50px;width:100%;height:50px;background:var(--black)}
.banner .logo-box{position:absolute;left:50%;top:11px;transform:translateX(-50%);width:60px;height:52px;background:var(--black);padding:6px;z-index:1}
.banner .logo-box span{display:flex;width:100%;height:100%;background:var(--white);align-items:center;justify-content:center;font-family:"Montserrat",Arial,sans-serif;font-weight:800;font-size:8.5px;text-align:center;line-height:1.05}
.banner .band-title{position:absolute;top:72px;width:100%;text-align:center;font-family:"Montserrat",Arial,sans-serif;font-weight:700;font-size:21px;color:var(--white);z-index:2}
.banner .body{position:absolute;top:104px;bottom:6px;left:50%;transform:translateX(-50%);width:210px;display:flex;flex-direction:column;justify-content:center;gap:8px}
.banner .body p{font-size:6.5px;line-height:1.45;text-align:center}

/* what we do */
.wwd .list{position:absolute;left:8px;top:12px;width:200px}
.wwd .list h4{font-size:6.2px;font-weight:700;margin-top:3px}
.wwd .list p{font-size:5.2px;line-height:1.35}
.wwd .heading{position:absolute;left:238px;top:12px;font-family:"Montserrat",Arial,sans-serif;font-weight:700;font-size:18px;line-height:1.2;text-align:right;width:54px}
.wwd .ph{position:absolute;width:84px;height:62px}
.wwd .p1{left:298px;top:8px;background:linear-gradient(135deg,#8b7a68,#d9c8ae)}
.wwd .p2{left:208px;top:80px;background:linear-gradient(135deg,#4e5648,#a6ae97)}
.wwd .p3{left:298px;top:80px;background:linear-gradient(135deg,#5c5c5c,#b8b1a5)}
.wwd .p4{left:208px;top:150px;background:linear-gradient(135deg,#5a3c26,#c5a47e)}
.wwd .p5{left:298px;top:150px;background:linear-gradient(135deg,#2b2420,#8a6a50)}
.wwd .p6{left:118px;top:150px;width:86px;background:linear-gradient(135deg,#3b3d36,#8f9080)}

/* services */
.services .photo{left:14px;top:0;width:118px;height:100%;background:linear-gradient(160deg,#a3968a,#3b3430)}
.services .bar{position:absolute;left:132px;top:0;width:18px;height:100%;background:var(--blue)}
.services .txt{position:absolute;left:160px;top:6px;width:228px}
.services .lead{font-size:5.4px;font-weight:700;text-align:center;line-height:1.35}
.services h4{font-size:5.6px;font-weight:700;margin-top:5px}
.services h4::before{content:"";display:inline-block;width:4px;height:4px;border:.6px solid var(--ink);margin-right:4px;vertical-align:middle}
.services p{font-size:5px;line-height:1.35;margin-top:2px}

/* levels */
.levels svg{position:absolute;left:0;top:0;width:100%;height:100%}
.levels .lab{font-family:"Montserrat",Arial,sans-serif;font-size:6px;font-weight:600;fill:#222;text-anchor:middle}
.levels .sub{font-family:"Montserrat",Arial,sans-serif;font-size:6px;fill:#333;text-anchor:middle}

/* destinations */
.dest .title{position:absolute;left:26px;top:18px;font-size:13px;line-height:1.25;font-weight:600}
.dest .worldmap{position:absolute;left:8px;top:58px;width:330px;height:160px;background:linear-gradient(90deg,#f08c2a 0%,#f4b63a 25%,#f6f6f6 40%,#c8102e 60%,#3ca53c 75%,#a3d977 100%);opacity:.85}
.dest .dots{position:absolute;right:18px;top:26px;display:flex;flex-direction:column;gap:11px}
.dest .dots i{display:block;width:11px;height:11px;border-radius:50%}
</style>
</head>
<body>
<main class="board">

  <!-- 1 cover -->
  <section class="slide cover1">
    <div class="photo" role="img" aria-label="Group of students with arms around each other, seen from behind"></div>
    <div class="logo-box"><span class="brand">KORVA<br>PATH</span></div>
    <h1 class="title">KORVA PATH</h1>
    <p class="subtitle">Universities Entrance Services</p>
    <p class="contacts">www.korvapath.ae info@korvapath.ae +971500000000 +971520000000 UAE,ABU DHABI</p>
  </section>

  <!-- 2 cover europe -->
  <section class="slide cover2">
    <div class="map" role="img" aria-label="Grey map of Europe"></div>
    <p class="brand">KORVA<br>PATH</p>
    <h1 class="title">KORVA PATH</h1>
    <p class="subtitle">Universities Entrance Services</p>
    <p class="contacts">www.korvapath.ae<br>info@korvapath.ae<br>+971 50 000 0000</p>
  </section>

  <!-- 3 cover world -->
  <section class="slide cover3">
    <div class="map" role="img" aria-label="Faint grey world map"></div>
    <p class="brand">KORVA<br>PATH</p>
    <h1 class="title">KORVA PATH</h1>
    <p class="subtitle">Universities Entrance Services</p>
    <p class="contacts">www.korvapath.ae<br>info@korvapath.ae<br>+971 50 000 0000</p>
  </section>

  <!-- 4 quotes -->
  <section class="slide">
    <div class="vline" style="left:72px;top:0;height:72px"></div>
    <div class="vline" style="left:322px;top:116px;height:106px"></div>
    <div class="portrait" style="left:280px;top:22px" role="img" aria-label="Black and white portrait of Amara Okonjo"></div>
    <div class="portrait warm" style="left:28px;top:118px" role="img" aria-label="Portrait of Dr. Faris Al Mansoori"></div>
    <p class="quote" style="left:132px;top:24px"><span class="mark">“</span>Education is the most powerful weapon which you can use to change the world<span class="mark">”</span><span class="by">Amara Okonjo</span></p>
    <p class="quote" style="left:132px;top:120px"><span class="mark">“</span>There is no place in the future for those who lack science and knowledge<span class="mark">”</span><span class="by">Dr. Faris Al Mansoori</span></p>
    <span class="corner-brand">KORVA PATH</span>
  </section>

  <!-- 5 quotes dark -->
  <section class="slide">
    <div class="vline dark" style="left:72px;top:0;height:118px"></div>
    <div class="vline dark" style="left:322px;top:110px;height:112px"></div>
    <div class="portrait dark" style="left:280px;top:22px" role="img" aria-label="Black and white portrait of Amara Okonjo"></div>
    <div class="portrait warm dark" style="left:28px;top:118px" role="img" aria-label="Portrait of Dr. Faris Al Mansoori"></div>
    <p class="quote" style="left:132px;top:24px"><span class="mark" style="color:#111">“</span>Education is the most powerful weapon which you can use to change the world<span class="mark" style="color:#111">”</span><span class="by">Amara Okonjo</span></p>
    <p class="quote" style="left:132px;top:120px"><span class="mark" style="color:#111">“</span>There is no place in the future for those who lack science and knowledge<span class="mark" style="color:#111">”</span><span class="by">Dr. Faris Al Mansoori</span></p>
    <span class="corner-brand">KORVA PATH</span>
  </section>

  <!-- 6 quotes horizontal -->
  <section class="slide">
    <div class="hline" style="left:0;top:81px;width:118px"></div>
    <div class="hline" style="left:300px;top:168px;width:95px"></div>
    <div class="portrait warm dark" style="left:116px;top:38px" role="img" aria-label="Portrait of Dr. Faris Al Mansoori"></div>
    <div class="portrait dark" style="left:192px;top:126px" role="img" aria-label="Black and white portrait of Amara Okonjo"></div>
    <p class="quote" style="left:238px;top:46px"><span class="mark" style="color:#111">“</span>There is no place in the future for those who lack science and knowledge<span class="mark" style="color:#111">”</span><span class="by">Dr. Faris Al Mansoori</span></p>
    <p class="quote" style="left:16px;top:136px"><span class="mark" style="color:#111">“</span>Education is the most powerful weapon which you can use to change the world<span class="mark" style="color:#111">”</span><span class="by">Amara Okonjo</span></p>
    <span class="corner-brand">KORVA PATH</span>
  </section>

  <!-- 7 overview -->
  <section class="slide overview">
    <div class="strip" role="img" aria-label="Four photos of students and consultants meeting at tables"><div></div><div></div><div></div><div></div></div>
    <div class="tags"><span class="tag">WHO ARE WE</span><span class="tag">VISION</span><span class="tag">MISSION</span><span class="tag">OUR VALUES</span></div>
    <div class="cols">
      <p>KORVA PATH is the fastest growing educational consultancy and study abroad services in UAE. It is officially recognized by Ministry of Education and Scientific Research, Global Language Board, EduAgent Network and QA-9000. Established in 2015. KORVA PATH provides professional consultancy services to help aspiring students find a suitable overseas educational institution in USA, UK, Australia, Malaysia, Europe, Middle East, South Africa and more. We take pride in our holistic program that helps every student make the right career choice, find the right course, what the student need and the government vision.</p>
      <p>To be leading the educational consultancy in the region by providing customized and up to date educational services to students and educational institutions abroad.</p>
      <p>To provide students from all the countries with the needed and qualified services for abroad studies through an integrated system of facilities, consultancy services and guidance through building strategic partnerships with the best universities from all over the world.</p>
      <p>Credibility Social Responsibility Excellence in Services delivery Strengthening Partnerships Implementing best practices in the educational consultancy.</p>
    </div>
  </section>

  <!-- 8 who are we -->
  <section class="slide banner">
    <div class="band"></div>
    <div class="logo-box"><span>KORVA<br>PATH</span></div>
    <h2 class="band-title">WHO ARE WE</h2>
    <div class="body">
      <p>KORVA PATH is the fastest growing educational consultancy and study abroad services in UAE. It is officially recognized by Ministry of Education and Scientific Research, Global Language Board, EduAgent Network and QA-9000. Established in 2015.</p>
      <p>KORVA PATH provides professional consultancy services to help aspiring students find a suitable overseas educational institution in USA, UK, Australia, Malaysia, Europe, Middle East, South Africa and more. We take pride in our holistic program that helps every student make the right career choice, find the right course, what the student need and the government vision. We act as study abroad consultants for various government sectors and corporations.</p>
    </div>
  </section>

  <!-- 9 vision -->
  <section class="slide banner">
    <div class="band"></div>
    <div class="logo-box"><span>KORVA<br>PATH</span></div>
    <h2 class="band-title">VISION</h2>
    <div class="body" style="width:200px;top:110px;bottom:60px">
      <p>To be leading the educational consultancy in the region by providing customized and up to date educational services to students and educational institutions abroad.</p>
    </div>
  </section>

  <!-- 10 mission -->
  <section class="slide banner">
    <div class="band"></div>
    <div class="logo-box"><span>KORVA<br>PATH</span></div>
    <h2 class="band-title">MISSION</h2>
    <div class="body" style="width:160px;top:110px;bottom:40px">
      <p>To provide students from all the countries with the needed and qualified services for abroad studies through an integrated system of facilities, consultancy services and guidance through building strategic partnerships with the best universities from all over the world.</p>
    </div>
  </section>

  <!-- 11 values -->
  <section class="slide banner">
    <div class="band"></div>
    <div class="logo-box"><span>KORVA<br>PATH</span></div>
    <h2 class="band-title">OUR VALUES</h2>
    <div class="body" style="width:190px;top:120px;bottom:30px">
      <p>Credibility Social Responsibility Excellence in Services delivery Strengthening Partnerships Implementing best practices in the educational consultancy.</p>
    </div>
  </section>

  <!-- 12 what we do -->
  <section class="slide wwd">
    <div class="list">
      <h4>FREE Academic Consulting</h4>
      <p>We get to understand the student's academic, social, and personal backgrounds and then provide them with various career options.</p>
      <h4>Course Selection</h4>
      <p>We assist our students in finding them right and correct courses based on their interests. Courses that are suitable to the industry in uplifting their professional levels for a successful career.</p>
      <h4>Application submission</h4>
      <p>We help save the students' time and energy by providing advice through the entire process of application, with required documents, deadlines and statement editing.</p>
      <h4>University Selection</h4>
      <p style="width:108px">Selecting a university involves a holistic look at all aspects of an institution including facilities and future prospects. We guide our students.</p>
      <h4>Quick Admission Decision</h4>
      <p style="width:108px">KORVA PATH makes it easy for students by contacting universities for timely offers and resolving all minor issues.</p>
    </div>
    <h2 class="heading">WHAT WE DO</h2>
    <div class="ph p1" role="img" aria-label="Students at an education fair"></div>
    <div class="ph p2" role="img" aria-label="Student working on a laptop outdoors"></div>
    <div class="ph p3" role="img" aria-label="Consultant meeting with a student"></div>
    <div class="ph p4" role="img" aria-label="Graduation ceremony hall"></div>
    <div class="ph p5" role="img" aria-label="Graduates on stage"></div>
    <div class="ph p6" role="img" aria-label="Large university library reading room"></div>
  </section>

  <!-- 13 services -->
  <section class="slide services">
    <div class="photo" role="img" aria-label="Group photo of smiling students"></div>
    <div class="bar"></div>
    <div class="txt">
      <p class="lead">KORVA PATH offers professional consultation to local and international students on a wide variety of educational programs covering summer and English programs, pathway courses, undergraduate, postgraduate degree programs and PHD courses. We help students through each stage</p>
      <h4>Scholarship Advice</h4>
      <p>We help our students in advising them to various scholarships offered by universities and government sectors and assist them with the entire application process</p>
      <h4>Accommodation</h4>
      <p>We assist our students by providing information on various accommodations like on campus, off campus, homestays, student housing, residential accommodation and so forth.</p>
      <h4>Visa assistance</h4>
      <p>Applying for visa is a critical part of overseas education preparation. Our consultants provide a checklist for visa processing and prepare students for visa interviews.</p>
      <h4>Other Services</h4>
      <p>Our other services include organizing insurance, airport pick-ups, pre-departure advice and more to make the journey hassle free and comfortable.</p>
      <h4>Languages and Preparation programs</h4>
      <p>Our tie up connections with colleges and language schools offer courses that help in meeting the essential requirements at various universities for admission.</p>
    </div>
  </section>

  <!-- 14 levels -->
  <section class="slide levels">
    <svg viewBox="0 0 395 222" aria-label="Study levels from foundation to PhD">
      <g fill="none" stroke-width="7">
        <path d="M24 176 V150 H96" stroke="#000"/>
        <path d="M109 152 V126 H185" stroke="#000"/>
        <path d="M196 126 V100 H268" stroke="#0555a3"/>
        <path d="M280 104 V78 H350" stroke="#aaaaaa"/>
      </g>
      <g>
        <polygon points="98,152 108,142 108,152" fill="#000"/>
        <polygon points="186,128 196,118 196,128" fill="#000"/>
        <polygon points="270,102 280,92 280,102" fill="#0555a3"/>
        <polygon points="352,80 362,70 362,80" fill="#aaaaaa"/>
      </g>
      <circle cx="60" cy="174" r="17" fill="#000"/>
      <circle cx="147" cy="150" r="17" fill="#000"/>
      <circle cx="232" cy="124" r="17" fill="#0555a3"/>
      <circle cx="316" cy="102" r="17" fill="#aaaaaa"/>
      <text class="lab" x="60" y="202">FOUNDATION /</text>
      <text class="lab" x="60" y="211">PATHWAY COURSES</text>
      <text class="lab" x="60" y="220">ENGLISH LANGUAGE</text>
      <text class="lab" x="147" y="180">UNDERGRADUATE DEGREE</text>
      <text class="sub" x="147" y="190">– Bachelor's Degree</text>
      <text class="sub" x="147" y="202">( 3 to 4 years )</text>
      <text class="lab" x="232" y="154">MASTERS DEGREE</text>
      <text class="sub" x="232" y="165">( 1 to 2 years )</text>
      <text class="lab" x="232" y="177">MBA</text>
      <text class="sub" x="232" y="190">( 1 to 2 years )</text>
      <text class="lab" x="316" y="132">PHD / DBA</text>
      <text class="sub" x="316" y="145">(3 – 4 YEARS)</text>
      <text x="386" y="212" font-family="Montserrat, Arial, sans-serif" font-weight="800" font-size="8" text-anchor="end">KORVA PATH</text>
    </svg>
  </section>

  <!-- 15 destinations -->
  <section class="slide dest">
    <h2 class="title">STUDY<br>DESTINATION</h2>
    <div class="worldmap" role="img" aria-label="World map with study destination countries coloured: North America orange and yellow, Europe and Russia red, China green, Australia light green"></div>
    <div class="dots">
      <i style="background:#f07f1a"></i>
      <i style="background:#f5b62c"></i>
      <i style="background:#c8102e"></i>
      <i style="background:#4f8f3a"></i>
      <i style="background:#22b022"></i>
      <i style="background:#7a1fd1"></i>
      <i style="background:#0b2a6f"></i>
      <i style="background:#f2ea1a"></i>
      <i style="background:#a3d977"></i>
    </div>
  </section>

</main>
</body>
</html>
```